Looking for someone to design a business card for my plumbing business Quandor Plumbing Solutions I want the background also to be black, must attract clients. If possible I want the front to be the logo and the back to show maybe the details.

Target Market(s)

Clients

Industry/Entity Type

Plumbing maintenance

Contact Information for Business Card

Name: Felix, Contact: 0461 539 207, Email: quandorplumbingsolutions@mailbrook.example, Licence number 728093K

Font styles to use
Other font styles liked:
• as per logo maybe?

Colors

Designer to choose colors to be used in the design.

Requirements
Nice to have
• stating the service I provide, emergency plumbing, plumbing maintenance, drainage maintenance, block sewer and stormwater, camera and locating.

```html
<!DOCTYPE html>
<html lang="en">
<head>
<meta charset="utf-8">
<title>Quandor Plumbing Solutions – Business Card</title>
<link rel="stylesheet" href="https://fonts.googleapis.com/css2?family=Montserrat:wght@400;500;700;800&display=swap">
<style>
  :root {
    --page: #151515;
    --card: #1f1f1f;
    --card-faint: #262626;
    --brand-blue: #4a8ccc;
    --ink: #f1f1f1;
    --ink-soft: #e2e2e2;
  }
  * { margin: 0; padding: 0; box-sizing: border-box; }
  html, body {
    width: 1200px; height: 1059px; overflow: hidden;
    background: var(--page);
    font-family: "Montserrat", Arial, sans-serif;
    color: var(--ink);
  }
  .canvas { position: relative; width: 1200px; height: 1059px; }
  .card {
    position: absolute;
    background: var(--card);
    border-radius: 18px;
    overflow: hidden;
  }
  .card--details { left: 257px; top: 89px; width: 687px; height: 390px; }
  .card--brand { left: 254px; top: 547px; width: 693px; height: 393px; }

  .wordmark {
    position: absolute;
    display: flex; align-items: center; gap: 12px;
  }
  .wordmark__square { background: var(--brand-blue); flex: none; }
  .wordmark__name {
    font-weight: 800; text-transform: uppercase; color: var(--ink);
    line-height: 1.05; letter-spacing: 0.5px;
  }
  .card--details .wordmark { left: 40px; top: 52px; }
  .card--details .wordmark__square { width: 18px; height: 18px; }
  .card--details .wordmark__name { font-size: 30px; }

  .watermark-name {
    position: absolute; right: 24px; top: 40px;
    font-weight: 800; font-size: 96px; line-height: 0.95;
    text-transform: uppercase; color: var(--card-faint);
    text-align: right; letter-spacing: -1px;
  }

  .accent-bar {
    position: absolute; left: 0; top: 199px;
    width: 18px; height: 34px; background: var(--brand-blue);
  }
  .person { position: absolute; left: 41px; top: 195px; }
  .person__name {
    font-weight: 700; font-size: 25px; line-height: 1;
    color: var(--brand-blue); text-transform: uppercase; letter-spacing: 0.3px;
  }
  .person__role { font-size: 15px; font-weight: 500; margin-top: 3px; color: var(--ink-soft); }
  .licence {
    position: absolute; left: 41px; top: 247px;
    font-size: 15.5px; font-weight: 500; color: var(--ink-soft);
  }
  .contact-list { position: absolute; left: 41px; top: 282px; list-style: none; }
  .contact-list li {
    display: flex; align-items: center; gap: 8px;
    font-size: 15.5px; font-weight: 500; color: var(--ink-soft);
    height: 26px;
  }
  .contact-list svg { width: 13px; height: 13px; flex: none; fill: var(--brand-blue); }

  .card--brand .wordmark {
    left: 50%; top: 50%; transform: translate(-50%, -50%); gap: 18px;
  }
  .card--brand .wordmark__square { width: 34px; height: 34px; }
  .card--brand .wordmark__name { font-size: 50px; }
</style>
</head>
<body>
<main class="canvas">

  <section class="card card--details" aria-label="Card details side">
    <div class="watermark-name" aria-hidden="true">Quandor</div>

    <div class="wordmark">
      <span class="wordmark__square"></span>
      <span class="wordmark__name">Quandor<br>Plumbing Solutions</span>
    </div>

    <span class="accent-bar"></span>
    <div class="person">
      <p class="person__name">Felix</p>
      <p class="person__role">Founder &amp; CEO</p>
    </div>

    <p class="licence">Licence number 728093K</p>

    <ul class="contact-list">
      <li>
        <svg viewBox="0 0 24 24" aria-hidden="true"><path d="M6.6 10.8a15.2 15.2 0 0 0 6.6 6.6l2.2-2.2a1 1 0 0 1 1-.25 11.4 11.4 0 0 0 3.6.57 1 1 0 0 1 1 1V20a1 1 0 0 1-1 1A17 17 0 0 1 3 4a1 1 0 0 1 1-1h3.5a1 1 0 0 1 1 1c0 1.25.2 2.45.57 3.57a1 1 0 0 1-.25 1z"/></svg>
        0461 539 207
      </li>
      <li>
        <svg viewBox="0 0 24 24" aria-hidden="true"><path d="M2 5h20v14H2z M2 5l10 8 10-8" fill="none" stroke="#4a8ccc" stroke-width="2.4"/></svg>
        quandorplumbingsolutions@mailbrook.example
      </li>
      <li>
        <svg viewBox="0 0 24 24" aria-hidden="true"><circle cx="12" cy="12" r="11"/></svg>
        @QuandorPlumbingSolutions
      </li>
    </ul>
  </section>

  <section class="card card--brand" aria-label="Card brand side">
    <div class="wordmark">
      <span class="wordmark__square"></span>
      <span class="wordmark__name">Quandor<br>Plumbing Solutions</span>
    </div>
  </section>

</main>
</body>
</html>
```